Brimsett Gardening Fresh New Website

We are looking to create a simple fresh website for our landscaping business. The website should appeal to a 'high end' audience. We deal with a lot of Embassies and affluent clients who have extremely large gardens that are meticulously maintained. The site is about communicating our excellent landscaping and customer service skills and encouraging new clients to reach out and engage us to take care of their gardens.

The website is basically going to be our business card, it will have almost no functionality other than two 'contact us' forms, one for smaller clients and one for more detailed projects.

The website will not have a lot of written content and will have to show photos of beautifully landscaped gardens.

The main logo in black will influence the site, however, we are open to all suggestions.

We are expecting to have the following pages:
Home Page
Services
About Us
Contact Us
Showcase (photo gallery of our work)

We need someone who can code it to wordpress and be available for minor changes over a number of days. They will be simple tweaks.

```html
<!DOCTYPE html>
<html lang="en">
<head>
<meta charset="utf-8">
<title>Brimsett Gardening</title>
<link href="https://fonts.googleapis.com/css2?family=Montserrat:wght@600;700&family=Poppins:wght@400;500;600;700&display=swap" rel="stylesheet">
<style>
:root{
  --gold:#a8791d;
  --gold-light:#c89a2e;
  --yellow:#f7ce3e;
  --ink:#141414;
  --text:#4a4a4a;
  --white:#ffffff;
  --footer:#1c1c1c;
  --line:#e6e6e6;
}
*{margin:0;padding:0;box-sizing:border-box}
html,body{width:1200px;height:3338px;overflow:hidden;background:var(--white)}
body{position:relative;font-family:"Poppins",sans-serif;color:var(--ink)}
.abs{position:absolute}

/* hero */
.hero{left:0;top:0;width:1200px;height:587px;background:linear-gradient(180deg,#5d6a4e 0%,#3f5a32 35%,#7b7a6c 62%,#3d5a2a 100%)}
.hero-shade{left:0;top:0;width:1200px;height:587px;background:rgba(0,0,0,.22)}
.nav-band{left:0;top:45px;width:1200px;height:61px;background:rgba(0,0,0,.55);border-top:1px solid var(--gold-light);border-bottom:1px solid var(--gold-light)}
.nav-link{top:66px;color:var(--white);font-size:14px;font-weight:500}
.nav-mark{left:552px;top:14px;width:122px;height:122px;border-radius:50%;background:#151515;border:2px solid var(--gold-light);display:flex;align-items:center;justify-content:center;text-align:center}
.nav-mark span{font-family:"Poppins",sans-serif;font-weight:500;font-size:11px;letter-spacing:3px;color:var(--gold-light);line-height:1.5}
.btn-contact{left:959px;top:57px;width:112px;height:37px;border-radius:19px;background:var(--yellow);color:var(--white);font-size:12px;font-weight:600;display:flex;align-items:center;justify-content:center}
.hero-title{left:0;top:240px;width:1200px;text-align:center;color:var(--white);font-family:"Poppins",sans-serif;font-weight:700;font-size:47px;line-height:53px;text-transform:uppercase}
.btn-pill{left:544px;top:424px;width:112px;height:39px;border-radius:20px;background:var(--gold);color:var(--white);font-size:12px;font-weight:600;display:flex;align-items:center;justify-content:center}
.scroll-cue{left:568px;top:554px;width:64px;height:64px;border-radius:50%;background:var(--white);box-shadow:0 4px 14px rgba(0,0,0,.15);display:flex;align-items:center;justify-content:center}

/* about */
.about-photo{left:120px;top:678px;width:485px;height:433px;background:radial-gradient(ellipse at 50% 45%,#b9bec4 0%,#d9dde0 45%,#a9c27a 78%,#ffffff 100%)}
.eyebrow{font-family:"Montserrat",sans-serif;font-weight:700;font-size:33px;line-height:40px}
.about-copy{left:611px;top:760px;width:450px}
.about-copy .gold{color:var(--gold)}
.rule{width:50px;height:2px;background:var(--gold)}
.about-copy p{font-size:13px;line-height:22px;color:var(--text);margin-top:10px}
.btn-box{height:34px;background:var(--gold);color:var(--white);font-size:12px;font-weight:500;display:flex;align-items:center;justify-content:center}

/* section heads */
.section-head{left:0;width:1200px;text-align:center;font-family:"Montserrat",sans-serif;font-weight:700;font-size:33px}
.section-rule{left:575px;width:50px;height:2px;background:var(--gold)}

/* services */
.tab{top:1213px;width:158px;height:36px;font-size:12px;display:flex;align-items:center;justify-content:center}
.tab-active{left:434px;background:var(--yellow);color:var(--ink)}
.tab-idle{left:607px;background:var(--gold);color:var(--white)}
.services-bg{left:0;top:1348px;width:1200px;height:659px;background:linear-gradient(180deg,#ffffff 0%,#e7eadf 25%,#b7c29a 60%,#5f7a3a 100%)}
.card-photo{width:300px;height:240px}
.card-label{width:271px;height:55px;background:var(--white);display:flex;align-items:center;justify-content:center;gap:8px;font-weight:600;font-size:16px;box-shadow:0 2px 6px rgba(0,0,0,.08)}
.card-label i{display:block;width:34px;height:34px;border:2px solid var(--ink);border-radius:3px;background:var(--yellow)}
.card-label.active{background:var(--yellow);height:82px;flex-direction:column;gap:2px}
.card-label.active .row{display:flex;align-items:center;gap:8px}
.card-label.active a{font-size:12px;font-weight:500;color:var(--ink);text-decoration:underline}

/* testimonials */
.review{background:var(--white);border:1px solid var(--line);padding:20px 20px}
.review .who{display:flex;align-items:center;gap:12px}
.avatar{width:60px;height:60px;border-radius:50%;background:linear-gradient(135deg,#7fa7c9,#2c3b4a)}
.review h4{font-weight:500;font-size:16px}
.stars{color:var(--yellow);font-size:13px;letter-spacing:2px}
.review p{font-size:12.5px;line-height:21.5px;color:var(--text);margin-top:16px}
.review.featured{box-shadow:0 6px 18px rgba(0,0,0,.08);border-bottom:5px solid var(--gold)}
.arrow{top:2319px;width:44px;height:44px;border-radius:50%;background:var(--white);box-shadow:0 3px 10px rgba(0,0,0,.15);display:flex;align-items:center;justify-content:center}

/* gallery */
.shot{top:2607px;width:235px;height:247px}

/* footer */
.footer{left:0;top:3000px;width:1200px;height:338px;background:var(--footer);color:var(--white)}
.footer-name{left:120px;top:3130px;width:200px;text-align:center;font-family:"Poppins",sans-serif;font-weight:500;font-size:20px;letter-spacing:6px;line-height:30px;color:var(--gold-light)}
.footer-mark{left:200px;top:3062px;width:40px;height:40px;border-radius:50%;background:var(--gold-light)}
.social{top:3228px;width:28px;height:28px;border-radius:50%;border:1.5px solid var(--white)}
.foot-head{top:3051px;font-weight:600;font-size:15px;text-transform:uppercase}
.foot-rule{top:3077px;width:80px;height:1px;background:var(--gold)}
.foot-link{left:512px;font-size:13px}
.contact-row{left:849px;display:flex;gap:12px;font-size:13px;line-height:19px}
.contact-row svg{flex:none}
.foot-bottom{left:143px;top:3298px;width:915px;height:1px;background:#3a3a3a}
.copyright{left:0;top:3310px;width:1200px;text-align:center;font-size:12px}
</style>
</head>
<body>

<!-- hero -->
<div class="abs hero" role="img" aria-label="Formal garden with stone rotunda, paved circular path and clipped evergreen shrubs"></div>
<div class="abs hero-shade"></div>
<div class="abs nav-band"></div>
<div class="abs nav-link" style="left:153px">Home</div>
<div class="abs nav-link" style="left:273px">About Us</div>
<div class="abs nav-link" style="left:421px">Services</div>
<div class="abs nav-mark"><span>BRIMSETT<br>GARDENING</span></div>
<div class="abs nav-link" style="left:739px">Our Gallery</div>
<div class="abs btn-contact">CONTACT US</div>
<h1 class="abs hero-title">Brimsett Gardening<br>Your Full Landscaping &amp;<br>Lawn Care Experts</h1>
<div class="abs btn-pill">READ MORE</div>
<div class="abs scroll-cue">
  <svg width="24" height="38" viewBox="0 0 24 38"><rect x="2" y="2" width="20" height="34" rx="10" fill="none" stroke="#141414" stroke-width="2.5"/><line x1="12" y1="9" x2="12" y2="16" stroke="#141414" stroke-width="2.5" stroke-linecap="round"/></svg>
</div>

<!-- about -->
<div class="abs about-photo" role="img" aria-label="Large white clapboard house with porch and green lawn, faded at the edges"></div>
<div class="abs about-copy">
  <div class="eyebrow gold">ABOUT</div>
  <div class="eyebrow">BRIMSETT GARDENING</div>
  <div class="rule" style="margin-top:14px"></div>
  <p style="margin-top:18px">Duis aute irure dolor in reprehenderit in voluptate velit esse cillum dolore eu fugiat nulla pariatur.</p>
  <p>Lorem ipsum dolor sit amet, consectetur adipiscing elit, sed do amit eiusmod tempor incididunt ut labore et dolore magna aliqua. Ut enim ad minim veniam, quis nostrud exercitation ullamco laboris nisi ut aliquip ex ea commodo consequat.</p>
</div>
<div class="abs btn-box" style="left:610px;top:1028px;width:155px">READ MORE</div>

<!-- services -->
<h2 class="abs section-head" style="top:1136px">OUR SERVICES</h2>
<div class="abs section-rule" style="top:1188px"></div>
<div class="abs tab tab-active">LANDSCAPE SERVICE</div>
<div class="abs tab tab-idle">LAWN SERVICE</div>
<div class="abs services-bg" role="img" aria-label="Soft garden scene with wooden benches and lamp post"></div>

<div class="abs card-photo" style="left:141px;top:1280px;background:linear-gradient(180deg,#6f9fd2 0%,#b8cfe4 35%,#3f6b2c 60%,#5d9a35 100%)" role="img" aria-label="Manor house behind green trees and lawn"></div>
<div class="abs card-photo" style="left:450px;top:1280px;background:linear-gradient(180deg,#5b7a3a 0%,#9aa07a 50%,#8a8a80 75%,#4f6b2f 100%)" role="img" aria-label="Stone garden feature with mulch beds"></div>
<div class="abs card-photo" style="left:759px;top:1280px;background:linear-gradient(160deg,#4a3626 0%,#3a2a1d 60%,#5d4332 100%)" role="img" aria-label="Dark soil with trowel and potted seedlings"></div>
<div class="abs card-label" style="left:155px;top:1490px"><i></i>Design Service</div>
<div class="abs card-label active" style="left:464px;top:1490px">
  <div class="row"><i></i>Mulch or Rock Install</div>
  <a>Request A Quote →</a>
</div>
<div class="abs card-label" style="left:773px;top:1490px"><i></i>Grading Rough</div>

<div class="abs card-photo" style="left:141px;top:1595px;background:linear-gradient(180deg,#3f6b2c 0%,#c9ccc4 40%,#6aa03a 70%,#5b8e2f 100%)" role="img" aria-label="White villa on a wide lawn"></div>
<div class="abs card-photo" style="left:450px;top:1595px;background:linear-gradient(180deg,#2a4a6a 0%,#5a7a3a 30%,#7a6a4a 60%,#6a9a3a 100%)" role="img" aria-label="Rolls of fresh sod being laid"></div>
<div class="abs card-photo" style="left:759px;top:1595px;background:linear-gradient(180deg,#b9c0c6 0%,#4f7a3a 40%,#6a8e3f 70%,#9a9a9a 100%)" role="img" aria-label="Curved stone retaining wall with iron railing"></div>
<div class="abs card-label" style="left:155px;top:1805px"><i></i>Grading Final</div>
<div class="abs card-label" style="left:464px;top:1805px"><i></i>Sod Installation</div>
<div class="abs card-label" style="left:773px;top:1805px"><i></i>Retaining Walls</div>
<div class="abs btn-box" style="left:522px;top:1886px;width:153px">REQUEST A QUOTE</div>

<!-- testimonials -->
<h2 class="abs section-head" style="top:2082px">WHAT OUR CLIENTS SAY</h2>
<div class="abs section-rule" style="top:2135px"></div>

<div class="abs review" style="left:141px;top:2189px;width:300px;height:264px">
  <div class="who"><div class="avatar" role="img" aria-label="Client portrait"></div><div><h4>Oliver Hartley</h4><div class="stars">★★★★★</div></div></div>
  <p>Lorem ipsum dolor sit amet, consectetur adipiscing elit, sed do eiusmod tempor incididunt ut labore et dolore magna aliqua. Ut enim ad minim veniam ut aut reiciendis voluptatibus maiores alias ut aut reiciendis voluptatibus.</p>
</div>
<div class="abs review featured" style="left:450px;top:2160px;width:300px;height:290px">
  <div class="who"><div class="avatar" role="img" aria-label="Client portrait"></div><div><h4>Nadia Rowe</h4><div class="stars">★★★★★</div></div></div>
  <p>Sed ut perspiciatis unde omnis iste natus error sit voluptatem accusantium doloremque laudantium, totam rem aperiam, eaque ipsa quae ab illo AMIT inventore veritatis et quasi architecto beatae vitae dicta sunt explicabo. Nemo enim ipsam voluptatem.</p>
</div>
<div class="abs review" style="left:759px;top:2189px;width:300px;height:264px">
  <div class="who"><div class="avatar" role="img" aria-label="Client portrait"></div><div><h4>Tomas K</h4><div class="stars">★★★★★</div></div></div>
  <p>Lorem ipsum dolor sit amet, consectetur adipiscing elit, sed do eiusmod tempor incididunt ut labore et dolore magna aliqua. Ut enim ad minim veniam ut aut reiciendis voluptatibus maiores alias ut aut reiciendis voluptatibus.</p>
</div>
<div class="abs arrow" style="left:75px"><svg width="14" height="14" viewBox="0 0 14 14"><path d="M9 2 L4 7 L9 12" fill="none" stroke="#141414" stroke-width="2.4"/></svg></div>
<div class="abs arrow" style="left:1082px"><svg width="14" height="14" viewBox="0 0 14 14"><path d="M5 2 L10 7 L5 12" fill="none" stroke="#141414" stroke-width="2.4"/></svg></div>

<!-- gallery -->
<h2 class="abs section-head" style="top:2531px">WORK GALLERY</h2>
<div class="abs section-rule" style="top:2585px"></div>
<div class="abs shot" style="left:0;background:linear-gradient(180deg,#cfd9e0 0%,#c9a26a 40%,#8ab04a 60%,#6a9a2a 100%)" role="img" aria-label="Row of houses above a sunlit lawn"></div>
<div class="abs shot" style="left:241px;background:linear-gradient(180deg,#a0524a 0%,#7a6a55 35%,#5a4c3c 70%,#c9a53a 100%)" role="img" aria-label="Curved stone planter walls with flowers"></div>
<div class="abs shot" style="left:483px;background:linear-gradient(180deg,#d8d2c4 0%,#c6b79a 45%,#6f7a9a 75%,#4e6a3a 100%)" role="img" aria-label="Cottage front with flowering border"></div>
<div class="abs shot" style="left:724px;background:linear-gradient(180deg,#3f6a2a 0%,#b8424a 25%,#6a8e3a 50%,#9a7a6a 80%)" role="img" aria-label="Stone steps through flower garden"></div>
<div class="abs shot" style="left:965px;background:linear-gradient(180deg,#b9c0c6 0%,#3f6a2a 35%,#6a5a4a 60%,#4f8e2f 100%)" role="img" aria-label="Checkered path leading to a house"></div>
<div class="abs btn-box" style="left:522px;top:2880px;width:153px">VIEW ALL</div>

<!-- footer -->
<div class="abs footer"></div>
<div class="abs footer-mark"></div>
<div class="abs footer-name">BRIMSETT<br>GARDENING</div>
<div class="abs social" style="left:155px" aria-label="Social profile"></div>
<div class="abs social" style="left:190px" aria-label="Social profile"></div>
<div class="abs social" style="left:225px" aria-label="Social profile"></div>
<div class="abs social" style="left:260px" aria-label="Social profile"></div>

<div class="abs foot-head" style="left:512px;color:var(--white)">Quick Links</div>
<div class="abs foot-rule" style="left:512px"></div>
<div class="abs foot-link" style="top:3100px;color:var(--white)">Home</div>
<div class="abs foot-link" style="top:3136px;color:var(--white)">Services</div>
<div class="abs foot-link" style="top:3171px;color:var(--white)">Gallery</div>
<div class="abs foot-link" style="top:3207px;color:var(--white)">About Us</div>
<div class="abs foot-link" style="top:3243px;color:var(--white)">Contact Us</div>

<div class="abs foot-head" style="left:849px;color:var(--white)">Contact Details</div>
<div class="abs foot-rule" style="left:849px"></div>
<div class="abs contact-row" style="top:3098px;color:var(--white)">
  <svg width="28" height="28" viewBox="0 0 28 28"><path d="M14 3 C9 3 6 7 6 11 C6 17 14 25 14 25 C14 25 22 17 22 11 C22 7 19 3 14 3 Z" fill="none" stroke="#fff" stroke-width="1.6"/><circle cx="14" cy="11" r="3" fill="none" stroke="#fff" stroke-width="1.6"/></svg>
  <div>48 Larkspur Lane, Suite 2<br>Ashford, ST 40512</div>
</div>
<div class="abs contact-row" style="top:3160px;color:var(--white)">
  <svg width="28" height="28" viewBox="0 0 28 28"><path d="M7 4 L11 4 L13 10 L10 12 C11 15 13 17 16 18 L18 15 L24 17 L24 21 C24 23 22 24 20 24 C12 23 5 16 4 8 C4 6 5 4 7 4 Z" fill="none" stroke="#fff" stroke-width="1.6"/></svg>
  <div><b style="font-weight:500">Phone</b><br>(555) 318-2046</div>
</div>
<div class="abs contact-row" style="top:3223px;color:var(--white)">
  <svg width="28" height="28" viewBox="0 0 28 28"><rect x="3" y="7" width="22" height="16" fill="none" stroke="#fff" stroke-width="1.6"/><path d="M3 7 L14 16 L25 7" fill="none" stroke="#fff" stroke-width="1.6"/></svg>
  <div><b style="font-weight:500">Email</b><br>info@brimsettgardening.com</div>
</div>
<div class="abs foot-bottom"></div>
<div class="abs copyright" style="color:var(--white)">© 2024 Brimsett Gardening. All Rights Reserved</div>

</body>
</html>
```